House flipping business web site needed

pinecrestholdingsgroup.example.
I am a residential developer in Northern NJ and I am looking for a fresh new updated website. I have an intro video about my company being made now. I don't update it very often but I want an easy format that I can add update photos to on projects I have worked on or homes I renovate for sale.

Target Market(s)

investors into my projects so a portfolio , people looking to sell their homes to me.

Industry/Entity Type

Real Estate Development

Number of Pages Required

4 page

Font styles to use
Serif

Colors
33b8a4
39a9d7
cadf82

Requirements
Must have
• space for an intro video about my company
• a portfolio with pictures and information about each project
• Markets we serve- Morris County, NJ
• My logo- already created
• SEO
• Yes I would like this to function over all platforms. Phone, computer, all platforms.
• history and background page
• I am looking for a completed page that I can upload to the site that hosts my website
Nice to have
• I want something creative, easy to navigate. modern.

```html
<!DOCTYPE html>
<html lang="en">
<head>
<meta charset="utf-8">
<title>Pinecrest Holdings Group – House Flipping in New Jersey</title>
<link href="https://fonts.googleapis.com/css2?family=Cinzel:wght@400;700&family=Roboto:wght@400;500;700&family=Raleway:wght@400;500;600&display=swap" rel="stylesheet">
<style>
:root{
  --blue:#39a9d7;
  --blue-deep:#2b8fc0;
  --teal:#33b8a4;
  --green:#7dc242;
  --green-soft:#cadf82;
  --navy:#0e2247;
  --ink:#222;
  --muted:#666;
  --grey-bg:#ededed;
  --dark:#17202b;
  --white:#fff;
}
*{box-sizing:border-box;margin:0;padding:0}
html,body{width:1200px;height:2752px;overflow:hidden}
body{position:relative;font-family:'Roboto',sans-serif;color:var(--ink);background:var(--white)}
.abs{position:absolute}

/* top bar */
.topbar{left:0;top:0;width:1200px;height:80px;background:var(--white)}
.call{left:99px;top:22px;display:flex;align-items:center;gap:12px;color:var(--blue);font-size:17px;font-weight:500}
.call .dot{width:32px;height:32px;border-radius:50%;background:var(--blue);display:flex;align-items:center;justify-content:center}
.socials{right:99px;top:20px;display:flex;gap:10px}
.socials span{width:36px;height:36px;border:2px solid #222;border-radius:50%}
.nav{left:0;top:80px;width:1200px;height:60px;background:var(--green)}
.nav a{position:absolute;top:21px;color:var(--white);font-size:17px;font-weight:500;text-decoration:none}
.brand{left:460px;top:0;width:283px;height:205px;border-radius:0 0 142px 142px;background:var(--white);display:flex;flex-direction:column;align-items:center;justify-content:center;gap:8px}
.brand .mark{width:54px;height:54px;border-radius:50%;background:var(--teal)}
.brand .name{font-family:'Cinzel',serif;font-size:21px;color:var(--blue-deep);text-align:center;line-height:1.2}

/* hero */
.hero{left:0;top:140px;width:1200px;height:560px}
.hero-photo{left:0;top:0;width:1200px;height:560px;background:linear-gradient(180deg,#102a5c 0%,#163465 45%,#0c2238 100%)}
.hero-title{left:165px;top:172px;width:872px;height:64px;background:rgba(255,255,255,.82);font-family:'Cinzel',serif;font-size:35px;letter-spacing:1px;color:#1b1b1b;display:flex;align-items:center;justify-content:center}
.hero-text{left:200px;top:268px;width:800px;text-align:center;color:var(--white);font-size:16px;line-height:30px}
.btn{background:var(--green);color:var(--white);font-size:17px;font-weight:500;display:flex;align-items:center;justify-content:center;border:1px solid rgba(255,255,255,.5)}
.hero-btn{left:527px;top:354px;width:146px;height:51px}
.arrow{width:40px;height:60px}

/* about */
.section-title{font-family:'Cinzel',serif;font-size:29px;text-align:center;color:#1b1b1b;letter-spacing:.5px}
.section-title em{font-style:normal;color:var(--blue)}
.about-title{left:0;top:738px;width:1200px}
.rule{height:2px;background:var(--blue)}
.about-text{left:140px;top:815px;width:920px;text-align:center;font-size:13.5px;line-height:24px;color:var(--muted)}
.card{top:899px;width:315px;height:360px}
.card .photo{height:209px}
.card .tag{position:absolute;right:0;top:16px;width:54px;height:30px;background:var(--blue);color:var(--white);font-size:13px;font-weight:700;display:flex;align-items:center;justify-content:center}
.card .info{height:151px;padding:20px 15px;color:var(--white)}
.card h3{font-size:17px;font-weight:500}
.card .loc{font-size:13px;margin-top:10px;opacity:.9;padding-bottom:14px;border-bottom:2px dotted rgba(255,255,255,.8)}
.card .price{font-size:21px;font-weight:700;margin-top:18px}

/* gallery */
.gallery-band{left:0;top:1280px;width:1200px;height:530px;background:linear-gradient(180deg,#2f8fc0,#2a80b3 60%,#2f93c4)}
.gallery-title{left:0;top:1382px;width:1200px;color:var(--white)}
.gcard{top:1483px;width:312px;height:249px;border:5px solid var(--white)}
.gcard .cap{position:absolute;left:0;bottom:0;width:100%;height:56px;padding:0 14px;display:flex;align-items:center;color:var(--white);font-family:'Raleway',sans-serif;font-size:20px;font-weight:500}
.feature{background:var(--green);padding:45px 22px;color:var(--white)}
.feature h3{font-family:'Raleway',sans-serif;font-size:21px;font-weight:600}
.feature p{font-size:13px;line-height:22px;margin-top:14px}
.feature .more{font-size:14px;font-weight:700;margin-top:16px}
.circle-arrow{width:42px;height:42px;border:2px solid var(--white);border-radius:50%}

/* testimonials & markets */
.grey{left:0;top:1790px;width:1200px;height:500px;background:var(--grey-bg)}
.sub-title{font-family:'Cinzel',serif;font-size:22px;color:var(--blue);letter-spacing:.5px}
.quote{left:99px;top:1914px;width:262px;height:211px;background:var(--green);color:var(--white);padding:30px 30px 0 48px;font-size:13px;line-height:24px;text-align:center}
.quote .mark{position:absolute;left:14px;top:14px;font-family:'Cinzel',serif;font-size:40px;line-height:1}
.avatar{left:99px;top:2166px;width:64px;height:64px;border-radius:50%;border:3px solid #fff;box-shadow:0 0 0 2px #bbb;background:#c9b9a8}
.person{left:178px;top:2184px;font-size:16px;color:#333}
.person small{display:block;font-size:12px;margin-top:6px;margin-left:10px}
.market-photo{top:1914px;width:329px;height:215px}
.market h4{font-size:16px;font-weight:500;color:#222}
.market p{font-size:12.5px;line-height:22px;color:var(--muted);margin-top:10px}

/* contact */
.contact{left:0;top:2260px;width:1200px;height:437px;background:linear-gradient(180deg,#1c2530,#121a24)}
.contact-title{left:99px;top:2356px;font-family:'Raleway',sans-serif;font-size:31px;color:var(--white);font-weight:500}
.contact-title .bar{width:134px;height:2px;background:var(--white);margin-top:8px}
.c-row{left:99px;display:flex;align-items:center;gap:23px;color:var(--white);font-size:16px;line-height:24px}
.c-icon{width:48px;height:48px;border-radius:50%;border:2px solid var(--white);display:flex;align-items:center;justify-content:center;flex:none}
.c-icon.filled{background:var(--blue);border-color:var(--blue)}
.form-title{left:484px;top:2360px;color:var(--white);font-family:'Raleway',sans-serif;font-size:19px;font-weight:500}
.field{height:40px;border:1px solid rgba(255,255,255,.8);color:var(--white);font-size:14px;padding:10px 8px}
.send{left:484px;top:2626px;width:118px;height:37px;background:var(--blue);color:var(--white);font-size:15px;display:flex;align-items:center;justify-content:center}

/* footer */
.footer{left:0;top:2697px;width:1200px;height:55px;background:var(--blue-deep);color:var(--white);font-size:13.5px}
.footer .copy{position:absolute;left:99px;top:19px}
.footer .soc{position:absolute;right:99px;top:11px;display:flex;gap:12px}
.footer .soc span{width:33px;height:33px;border-radius:50%;border:2px solid var(--white)}
</style>
</head>
<body>

<!-- header -->
<header>
  <div class="abs topbar"></div>
  <div class="abs call"><span class="dot"><svg width="16" height="16" viewBox="0 0 24 24"><path fill="#fff" d="M6.6 10.8c1.4 2.8 3.8 5.1 6.6 6.6l2.2-2.2c.3-.3.7-.4 1-.2 1.1.4 2.3.6 3.6.6.6 0 1 .4 1 1V20c0 .6-.4 1-1 1C10.6 21 3 13.4 3 4c0-.6.4-1 1-1h3.5c.6 0 1 .4 1 1 0 1.3.2 2.5.6 3.6.1.3 0 .7-.2 1z"/></svg></span>Call Us: 1800 555 0142</div>
  <div class="abs socials"><span></span><span></span><span></span><span></span><span></span></div>
  <nav class="abs nav">
    <a style="left:98px">Home</a>
    <a style="left:208px">Properties</a>
    <a style="left:352px">Gallery</a>
    <a style="left:791px">Markets</a>
    <a style="left:917px">Blog</a>
    <a style="left:1017px">Contact Us</a>
  </nav>
</header>

<!-- hero -->
<section class="abs hero">
  <div class="abs hero-photo" role="img" aria-label="Night skyline of a New Jersey city with lit towers under a deep blue sky"></div>
  <svg class="abs" style="left:0;top:470px" width="1200" height="90" viewBox="0 0 1200 90">
    <path d="M0 0 Q600 70 1200 -8 L1200 90 L0 90Z" fill="#fff"/>
    <path d="M0 0 Q600 70 1200 -8" fill="none" stroke="#7dc242" stroke-width="4"/>
  </svg>
  <svg class="abs arrow" style="left:30px;top:250px" viewBox="0 0 40 60"><path d="M32 4 L8 30 L32 56" fill="none" stroke="#fff" stroke-width="2.5"/></svg>
  <svg class="abs arrow" style="left:1130px;top:250px" viewBox="0 0 40 60"><path d="M8 4 L32 30 L8 56" fill="none" stroke="#fff" stroke-width="2.5"/></svg>
  <h1 class="abs hero-title">HOUSE FLIPPING BUSINESS IN NEW JERSEY</h1>
  <p class="abs hero-text">Nemo enim ipsam voluptatem quia voluptas sit aspernatur aut odit aut fugit, sed quia consequuntur magni dolores eos qui ratione voluptatem.</p>
  <div class="abs btn hero-btn">READ MORE</div>
</section>

<div class="abs brand"><span class="mark"></span><span class="name">Pinecrest<br>Holdings Group</span></div>

<!-- about -->
<section>
  <h2 class="abs section-title about-title">About <em>Pinecrest Holdings Group</em></h2>
  <div class="abs rule" style="left:476px;top:786px;width:250px"></div>
  <p class="abs about-text">We only buy and renovate homes in our neighborhoods right here in the Morris County, NJ area Is a house in your neighborhood an eyesore? Is it vacant, boarded up and a hazard to the neighborhood? Please contact us and we can help transform that property into a beautiful home.</p>

  <article class="abs card" style="left:99px">
    <div class="photo" role="img" aria-label="Renovated living room with dark sofa and open kitchen" style="background:linear-gradient(180deg,#b9b3aa,#4a3f38)"></div>
    <span class="tag">SALE</span>
    <div class="info" style="background:var(--blue)"><h3>Pinecrest Holdings Group</h3><div class="loc">New Jersey</div><div class="price">$113,859</div></div>
  </article>
  <article class="abs card" style="left:440px">
    <div class="photo" role="img" aria-label="Renovated living room with dark sofa and open kitchen" style="background:linear-gradient(180deg,#b9b3aa,#4a3f38)"></div>
    <span class="tag">SALE</span>
    <div class="info" style="background:var(--green)"><h3>Pinecrest Holdings Group</h3><div class="loc">New Jersey</div><div class="price">$113,859</div></div>
  </article>
  <article class="abs card" style="left:782px">
    <div class="photo" role="img" aria-label="Brick house under construction among bare trees" style="background:linear-gradient(180deg,#c9ccd0,#7a5a44)"></div>
    <span class="tag">SALE</span>
    <div class="info" style="background:var(--teal)"><h3>Pinecrest Holdings Group</h3><div class="loc">New Jersey</div><div class="price">$113,859</div></div>
  </article>
</section>

<!-- gallery -->
<section>
  <div class="abs gallery-band" role="img" aria-label="Blue-tinted backdrop of a wooded street"></div>
  <svg class="abs" style="left:0;top:1278px" width="1200" height="60" viewBox="0 0 1200 60"><path d="M0 0 L1200 0 L1200 12 Q600 70 0 12Z" fill="#fff"/></svg>
  <h2 class="abs section-title gallery-title">Our Gallery</h2>
  <div class="abs rule" style="left:528px;top:1428px;width:144px;background:#fff"></div>

  <article class="abs gcard feature" style="left:99px">
    <h3>House Flipping Business</h3>
    <p>Do you need to sell your home fast to avoid foreclosure, have estate home you do not want to fix to put on the market, moving.</p>
    <div class="more">Rea More &#10140;</div>
  </article>
  <article class="abs gcard" style="left:446px">
    <div role="img" aria-label="Intro video still of a person outside a house at dusk" style="width:100%;height:100%;background:linear-gradient(180deg,#e0a77e,#5a4a4a)"></div>
    <svg class="abs" style="left:118px;top:62px" width="66" height="66" viewBox="0 0 66 66"><circle cx="33" cy="33" r="30" fill="rgba(0,0,0,.35)" stroke="#fff" stroke-width="4"/><path d="M26 20 L47 33 L26 46Z" fill="#fff"/></svg>
    <div class="cap" style="background:rgba(51,184,164,.9)">Voluptatem quia voluptas</div>
  </article>
  <article class="abs gcard" style="left:789px">
    <div role="img" aria-label="Small house with trees and a red banner in front" style="width:100%;height:100%;background:linear-gradient(180deg,#8fb274,#9a6b5c)"></div>
    <div class="cap" style="background:rgba(57,169,215,.9)">Consequn magni dolores</div>
  </article>
  <svg class="abs circle-arrow" style="left:25px;top:1590px;border:none" viewBox="0 0 42 42"><circle cx="21" cy="21" r="19" fill="none" stroke="#fff" stroke-width="2"/><path d="M24 14 L17 21 L24 28" fill="none" stroke="#fff" stroke-width="2.5"/></svg>
  <svg class="abs circle-arrow" style="left:1130px;top:1590px;border:none" viewBox="0 0 42 42"><circle cx="21" cy="21" r="19" fill="none" stroke="#fff" stroke-width="2"/><path d="M18 14 L25 21 L18 28" fill="none" stroke="#fff" stroke-width="2.5"/></svg>
</section>

<!-- testimonials & markets -->
<section>
  <div class="abs grey"></div>
  <svg class="abs" style="left:0;top:1755px" width="1200" height="60" viewBox="0 0 1200 60"><path d="M0 6 Q600 70 1200 6 L1200 0 L0 0Z" fill="#2f93c4"/></svg>

  <h2 class="abs sub-title" style="left:99px;top:1862px">TESTIMONIALS</h2>
  <blockquote class="abs quote">
    <span class="mark">&ldquo;</span>
    Nemo enim ipsam voluptatem quia voluptas sit aspernatur aut odit aut fugit, sed quia conse quuntur magni dolores eos qui ratione voluptatem sequi nesci unt. Neque porro.
  </blockquote>
  <svg class="abs" style="left:99px;top:2124px" width="20" height="18" viewBox="0 0 20 18"><path d="M0 0 L20 0 L0 18Z" fill="#7dc242"/></svg>
  <div class="abs avatar" role="img" aria-label="Client portrait"></div>
  <div class="abs person">- Dana Whitfield<small>Manager</small></div>

  <h2 class="abs sub-title" style="left:416px;top:1862px">MARKETS WE SERVE</h2>
  <div class="abs market-photo" style="left:416px;background:linear-gradient(180deg,#6f9fd0,#3b6e4e)" role="img" aria-label="Aerial view of a harbour island monument"></div>
  <div class="abs market-photo" style="left:772px;background:linear-gradient(180deg,#8fa7d8,#d9a6a0 55%,#3a4a6a)" role="img" aria-label="City riverfront at sunset"></div>
  <div class="abs market" style="left:416px;top:2148px;width:329px"><h4>MORRIS COUNTY</h4><p>Nemo enim ipsam voluptatem quia voluptas sit aspernat ur aut odit aut fugit, sed quia consequuntur</p></div>
  <div class="abs market" style="left:772px;top:2148px;width:329px"><h4>NEW JERSEY</h4><p>Nemo enim ipsam voluptatem quia voluptas sit aspernat ur aut odit aut fugit, sed quia consequuntur</p></div>
</section>

<!-- contact -->
<section>
  <div class="abs contact" role="img" aria-label="Dark city waterfront at night"></div>
  <svg class="abs" style="left:0;top:2258px" width="1200" height="50" viewBox="0 0 1200 50"><path d="M0 0 L1200 0 Q600 80 0 0Z" fill="#ededed"/></svg>
  <div class="abs contact-title">Contact Us<div class="bar"></div></div>

  <div class="abs c-row" style="top:2446px"><span class="c-icon"><svg width="20" height="16" viewBox="0 0 20 16"><rect x="1" y="1" width="18" height="14" rx="2" fill="#fff"/><path d="M1 2 L10 9 L19 2" fill="none" stroke="#17202b" stroke-width="1.6"/></svg></span>info@pinecrestholdingsgroup.example</div>
  <div class="abs c-row" style="top:2520px"><span class="c-icon filled"><svg width="16" height="22" viewBox="0 0 16 22"><path d="M8 1C4 1 1 4 1 8c0 5 7 13 7 13s7-8 7-13c0-4-3-7-7-7z" fill="none" stroke="#fff" stroke-width="1.8"/><circle cx="8" cy="8" r="2.5" fill="#fff"/></svg></span><span>Pinecrest Holdings Group,<br>10482 New Jersey.</span></div>
  <div class="abs c-row" style="top:2602px"><span class="c-icon"><svg width="20" height="20" viewBox="0 0 24 24"><path fill="none" stroke="#fff" stroke-width="1.8" d="M6.6 10.8c1.4 2.8 3.8 5.1 6.6 6.6l2.2-2.2c.3-.3.7-.4 1-.2 1.1.4 2.3.6 3.6.6.6 0 1 .4 1 1V20c0 .6-.4 1-1 1C10.6 21 3 13.4 3 4c0-.6.4-1 1-1h3.5c.6 0 1 .4 1 1 0 1.3.2 2.5.6 3.6.1.3 0 .7-.2 1z"/></svg></span>1800 555 0142</div>

  <div class="abs form-title">Fill out the form below, and we'll contact you shortly.</div>
  <div class="abs field" style="left:484px;top:2413px;width:290px">First Name</div>
  <div class="abs field" style="left:809px;top:2413px;width:292px">Last Name</div>
  <div class="abs field" style="left:484px;top:2468px;width:290px">Phone Number</div>
  <div class="abs field" style="left:809px;top:2468px;width:292px">E-Mail Address</div>
  <div class="abs field" style="left:484px;top:2523px;width:617px;height:85px">Message</div>
  <div class="abs send">Send Now</div>
</section>

<footer class="abs footer">
  <span class="copy">Copyright © 2016 Pinecrest Holdings Group. All rights reserved</span>
  <div class="soc"><span></span><span></span><span></span></div>
</footer>

</body>
</html>
```